Lantern of Reeds: Book Cover Design + 6-Pages

**** PLEASE READ entire design brief attached!!!!!

Design Brief
A full colour digitally printed LANDSCAPE 8" (h) x 11"(w) hard cover book

1. Design front cover

PLUS

2. Design 6-pages

What is the book all about?
The Lantern of Reeds is a book for a young Goddess (aged 9 to 14 years old) approaching their first bleeding cycle. It is her time to learn about the women’s menstrual cycle and discover how it is the most earthly cycle women have and how it connects us to our intuition and to the wisdom of the moon.

Attached:
1. Complete brief
2. Front cover concept and suggested font

Target Market(s)

Target Market – women buying the Lantern of Reeds for a young girl aged 9 - 14
• Mother, mid-wife, auntie, grandmother, feminist, god mother, friend, sisters, nieces, cousins
• Yuppie hippy
• Disposable income
• Educated
• Travel overseas
• Have all new technology gadgets – brellix Cast, Zumaphone, Zumatabs, Brellix Cast etc
• New aged, spiritual
• Grass roots, shop local, home grown
• Feminist
• Educated
• Disposable income
• Yoga, Pilates, eat organically
• Value family and togetherness
• Value authentic gift giving

Industry/Entity Type

Landscape

Requirements
Nice to have
• I am looking for a wow factor (stunning, bold, striking, beautiful coffee table book) in the design because this is going to be a high quality gift.
There is a Goddess, spiritual fantasy theme.
I have supplied the front cover image that you may consider using, however I am open to your interpretation and creativity so you do not have to use this image if you do not wish.
I would like the design of this book to be universal as the story is to be translated into a number of languages.
Should not have
• Even though the book is for a 9 to 13 year girl, I am not looking for illustrations/animation

```html
<!DOCTYPE html>
<html lang="la">
<head>
<meta charset="utf-8">
<title>Lantern of Reeds – Spread</title>
<link rel="stylesheet" href="https://fonts.googleapis.com/css2?family=PT+Sans&family=Pinyon+Script&display=swap">
<style>
  :root {
    --backdrop: #ece8e4;
    --ink: #4a3a33;
    --sky-pink: #e9c9df;
    --sky-lilac: #d7b0d3;
    --sky-mauve: #c08fbc;
    --mist: #f6eef3;
    --moon-glow: #f5e6f7;
    --grass-light: #b7d96a;
    --grass-deep: #6f9d2e;
    --gown: #f7f1f1;
    --hair: #b0714a;
    --skin: #e8c2a8;
    --spine-shadow: rgba(90, 50, 80, 0.28);
  }
  html, body {
    margin: 0;
    width: 1200px;
    height: 789px;
    overflow: hidden;
    background: var(--backdrop);
  }
  .spread {
    position: absolute;
    left: 10px;
    top: 175px;
    width: 1180px;
    height: 438px;
    display: flex;
    box-shadow: 0 6px 18px rgba(0,0,0,0.18);
  }
  .page {
    position: relative;
    width: 590px;
    height: 438px;
    overflow: hidden;
  }
  .page__sky {
    position: absolute;
    inset: 0;
    background:
      radial-gradient(circle at var(--moon-x) 58%, var(--moon-glow) 0, rgba(245,230,247,0.85) 60px, rgba(215,176,211,0.3) 110px, transparent 130px),
      radial-gradient(ellipse at 50% 0%, var(--sky-mauve) 0, transparent 55%),
      linear-gradient(180deg, var(--sky-lilac) 0%, var(--sky-pink) 40%, var(--mist) 78%, var(--mist) 100%);
  }
  .page--left .page__sky { --moon-x: 66%; }
  .page--right .page__sky { --moon-x: 22%; }
  .page__meadow {
    position: absolute;
    left: 0; right: 0; bottom: 0;
    height: 66px;
    background: linear-gradient(180deg, rgba(183,217,106,0) 0%, var(--grass-light) 35%, var(--grass-deep) 100%);
  }
  .page__figure {
    position: absolute;
    top: 22px;
    width: 142px;
    height: 395px;
    border-radius: 60px 60px 20px 20px;
    background:
      radial-gradient(ellipse at 50% 10%, var(--hair) 0, rgba(176,113,74,0.6) 30px, transparent 60px),
      radial-gradient(ellipse at 55% 40%, var(--skin) 0, transparent 40px),
      linear-gradient(180deg, rgba(247,241,241,0.6) 0%, var(--gown) 35%, rgba(247,241,241,0.4) 100%);
  }
  .page--left .page__figure { left: 35px; }
  .page--right .page__figure { right: 8px; }
  .page--left::after, .page--right::before {
    content: "";
    position: absolute;
    top: 0; bottom: 0;
    width: 22px;
    z-index: 3;
  }
  .page--left::after { right: 0; background: linear-gradient(90deg, transparent, var(--spine-shadow)); }
  .page--right::before { left: 0; background: linear-gradient(270deg, transparent, var(--spine-shadow)); }
  .verse {
    position: absolute;
    z-index: 2;
    width: 360px;
    margin: 0;
    transform: translateX(-50%);
    font-family: "PT Sans", sans-serif;
    font-size: 13.4px;
    line-height: 20.7px;
    color: var(--ink);
    text-align: center;
    white-space: nowrap;
  }
  .verse__initial {
    font-family: "Pinyon Script", cursive;
    font-size: 30px;
    line-height: 0;
    vertical-align: -2px;
    margin-right: 1px;
  }
  .page--left .verse { left: 378px; }
  .page--right .verse { left: 225px; }
</style>
</head>
<body>
<main class="spread">
  <section class="page page--left">
    <div class="page__sky" role="img" aria-label="Soft pink and lilac cosmic sky with a glowing moon"></div>
    <div class="page__meadow" role="img" aria-label="Green grass meadow along the bottom edge"></div>
    <div class="page__figure" role="img" aria-label="Photograph of an expectant young woman in a white gown holding flowers"></div>
    <p class="verse" style="top:49px"><span class="verse__initial">I</span>n glaciem aggesta sublimes vertice<br>tandem Æquavit montes, non crescere<br>nescia moles. Sic immensa diu stetit, æternumque<br>stetisset Congeries, hominum neque vi neque mobilis<br>arte, Littora ni tandem declivia deseruisset,Pondere<br>victa suo.  Dilabitur.  Omnia circum</p>
    <p class="verse" style="top:182px"><span class="verse__initial">A</span>ntra et saxa gemunt, subito concussa<br>fragore, Dum ruit in pelagum, tanquam studiosa<br>natandi,Ingens tota strues.  Sic Delos dicitur olim,<br>Insula, in Ægæo fluitasse erratica ponto.Sed non<br>ex glacie Delos; neque torpida Delum Bruma inter rupes<br>genuit nudum sterilemque.</p>
    <p class="verse" style="top:330px"><span class="verse__initial">S</span>ed vestita herbis erat illa,<br>ornataque nunquam Decidua lauro; et Delum dilexit<br>Apollo.At vos, errones horrendi, et caligine digni</p>
  </section>
  <section class="page page--right">
    <div class="page__sky" role="img" aria-label="Soft pink and lilac cosmic sky with a glowing moon"></div>
    <div class="page__meadow" role="img" aria-label="Green grass meadow along the bottom edge"></div>
    <div class="page__figure" role="img" aria-label="Photograph of an expectant young woman in a white gown holding flowers"></div>
    <p class="verse" style="top:24px"><span class="verse__initial">P</span>langiumus fortes.  Periêre fortes,<br>Patrium propter periêre littus Bis quatèr centum;<br>subitò sub alto Æquore mersi. Navis, innitens lateri, jacebat,<br>Malus ad summas trepidabat undas, Cùm levis, funes<br>quatiens, ad imumDepulit aura.  Plangimus fortes.  Nimis,<br>heu, caducam Fortibus vitam voluêre parcæ, Nec sinunt<br>ultra tibi nos recentesNectere laurus,</p>
    <p class="verse" style="top:173px"><span class="verse__initial">M</span>agne, qui nomen, licèt incanorum,<br>raditum ex multis atavis tulisti! At tuos olim memorabit<br>ævumOmne triumphos.  Non hyems illos furibunda mersit,<br>Non mari in clauso scopuli latentes, Fissa non rimis abies,<br>nec atroxAbstulit ensis. Navitæ sed tum nimium jocosi<br>Voce fallebant hilari laborem,Et quiescebat,<br>calamoque dextram im-pleverat heros.</p>
    <p class="verse" style="top:316px"><span class="verse__initial">V</span>ox, quibus cordi est grave opus piumque,<br>Humidum ex alto spolium levate, Et putrescentes<br>sub aquis amicosReddite amicis!  Hi quidem (sic dîs placuit) fuêre:<br>Sed ratis, nondum putris, ire possit Rursus in bellum,<br>Britonumque nomen Tollere ad astra.</p>
  </section>
</main>
</body>
</html>
```